Design a single page Shopify store web page

We are looking to have a page designed for a single page Shopify store with 2 products. We already have a basic structure that we like, though we are open to suggestions. We are looking for somebody to provide a design/color scheme that we can then implement using Shopify's templating system. We can handle the implementation(HTML / CSS / jS) as we already have 2 web developers on the team, but have not been able to find a design we liked.

The job would consist of providing a mockup (photoshop or otherwise) and any vector graphics you choose to create for the site (we can provide product photos and other images).

You can also look at http://brickdune.com.au for some of our design direction we have used so far

Target Market(s)

Young Australian Males (18 - 49)

Industry/Entity Type

Store

Number of Pages Required

1 page

Font styles to use
Serif
Sans Serif

Requirements
Must have
• Single Page Design
• E-commerce Product Purchase
• Manly (whatever interpretation of that you have)

```html
<!DOCTYPE html>
<html lang="en">
<head>
<meta charset="utf-8">
<title>Brick Dune — Underwear &amp; Socks Delivered</title>
<link rel="stylesheet" href="https://fonts.googleapis.com/css2?family=PT+Sans:wght@400;700&family=Open+Sans:wght@400;600;700&display=swap">
<style>
:root{
  --navy:#12304a;
  --navy-deep:#0b1a2a;
  --ink:#1f4e6e;
  --sky:#2cb5e8;
  --pink:#e8415e;
  --red:#e64f42;
  --faq-red:#c9302c;
  --green:#5cb85c;
  --grey:#777;
  --white:#fff;
}
*{margin:0;padding:0;box-sizing:border-box}
html,body{width:1200px;height:2335px;overflow:hidden;background:var(--white)}
body{position:relative;font-family:"Open Sans",sans-serif;color:#333}

/* header */
.site-header{position:absolute;left:0;top:0;width:1200px;height:109px;background:linear-gradient(#0f2438,#17324b)}
.brand{position:absolute;left:134px;top:32px;font-family:"PT Sans",sans-serif;font-size:42px;line-height:44px;letter-spacing:3px;color:#cfd8e3;font-weight:400}
.main-nav a{position:absolute;top:54px;font-size:15px;color:var(--white);text-decoration:none}
.signup{position:absolute;left:938px;top:42px;width:127px;height:36px;border:2px solid var(--sky);color:var(--sky);font-size:15px;text-align:center;line-height:32px}

/* hero */
.hero{position:absolute;left:0;top:109px;width:1200px;height:518px;overflow:hidden}
.hero-photo{position:absolute;inset:0;background:radial-gradient(circle at 30% 40%,#f2f2f2,#c9c9c9 70%,#a9a9a9)}
.hero svg{position:absolute;left:0;top:0}
.hero-copy{position:absolute;right:132px;text-align:right;color:var(--white);white-space:nowrap}
.hero-copy .accent{color:var(--sky)}
.hero-cta{position:absolute;left:910px;top:386px;width:158px;height:48px;background:var(--pink);color:var(--white);font-size:18px;line-height:48px;text-align:center}
.slider-dots{position:absolute;left:563px;top:654px;display:flex;gap:6px}
.slider-dots span{width:14px;height:14px;border-radius:50%;background:var(--navy)}
.slider-dots span:first-child{background:#ccc}

/* sections */
.section-title{position:absolute;left:0;width:1200px;text-align:center;font-family:"PT Sans",sans-serif;font-size:29px}
.divider{position:absolute;left:370px;width:460px;height:14px}
.step{position:absolute;width:330px;text-align:center}
.step-icon{width:94px;height:94px;border-radius:50%;margin:0 auto;background:radial-gradient(circle at 50% 35%,#f4f4f6,#c3c3c9);display:flex;align-items:center;justify-content:center}
.step h3{margin-top:26px;font-family:"PT Sans",sans-serif;font-size:22px;color:var(--ink);font-weight:700}
.step p{margin-top:12px;font-size:13px;line-height:21px;color:var(--grey)}

.plans{position:absolute;left:0;top:1069px;width:1200px;height:515px;background:var(--red);overflow:hidden}
.plan-card{position:absolute;top:137px;width:337px;height:332px;background:var(--white)}
.plan-card h3{position:absolute;top:28px;width:100%;text-align:center;font-weight:400;font-size:23px;color:#222}
.product-shot{position:absolute;border:1px solid #ddd}
.price{position:absolute;left:159px;top:279px;font-size:26px;color:#222;font-family:"PT Sans",sans-serif}
.get-it{position:absolute;left:221px;top:276px;width:93px;height:32px;background:var(--green);color:var(--white);font-size:15px;font-weight:600;text-align:center;line-height:32px}
.perks{position:absolute;left:867px;top:137px;width:200px;list-style:none}
.perks li{height:37px;border-bottom:1px solid rgba(255,255,255,.25);color:var(--white);font-weight:700;font-size:14px;white-space:nowrap;display:flex;align-items:center;gap:8px}
.perks li::before{content:"✔";color:#f7d23e;font-size:12px}

.faq-card{position:absolute;width:300px;height:176px;background:linear-gradient(#efefef,#fff);text-align:center;padding:0 18px}
.faq-card h4{font-weight:400;font-size:19px;line-height:26px;color:var(--faq-red);display:flex;align-items:center;justify-content:center;height:82px;padding-top:10px}
.faq-card p{font-size:13px;line-height:25px;color:#666}

.site-footer{position:absolute;left:0;top:2219px;width:1200px;height:116px;background:var(--navy-deep)}
.site-footer .links,.site-footer .email{position:absolute;top:52px;font-size:14px;color:var(--white)}
.social{position:absolute;top:47px;width:33px;height:33px}
.pay{position:absolute;width:37px;height:24px;top:52px;border-radius:2px}
</style>
</head>
<body>

<header class="site-header">
  <div class="brand">BRICK DUNE</div>
  <nav class="main-nav">
    <a style="left:565px">How It Works</a>
    <a style="left:689px">Plans</a>
    <a style="left:761px">FQA</a>
    <a style="left:825px">About Us</a>
  </nav>
  <div class="signup">Sign Up Now</div>
</header>

<section class="hero">
  <div class="hero-photo" role="img" aria-label="Photo of a man modelling white boxer briefs against a light wall"></div>
  <svg width="1200" height="518" viewBox="0 0 1200 518"><polygon points="817,0 1200,0 1200,518 506,518" fill="#12304a"/></svg>
  <div class="hero-copy" style="top:70px;font-size:43px;font-weight:700">AUTOMATE</div>
  <div class="hero-copy" style="top:126px;font-size:34px">YOUR LIFE</div>
  <div class="hero-copy" style="top:210px;font-size:26px;line-height:35px">
    <span class="accent">NEW</span> UNDERWEAR<br>
    <span class="accent">&amp;</span> SOCKS<br>
    <span class="accent">DELIVERED TO YOUR DOOR</span><br>
    WHEN YOU NEED IT
  </div>
  <div class="hero-cta">Yes Please!</div>
</section>
<div class="slider-dots"><span></span><span></span><span></span><span></span></div>

<section class="how-it-works">
  <h2 class="section-title" style="top:732px;color:#444;font-weight:400">How It <b style="color:var(--ink)">Works</b></h2>
  <svg class="divider" style="top:779px" viewBox="0 0 460 14"><line x1="0" y1="7" x2="205" y2="7" stroke="#e2e2e2"/><line x1="255" y1="7" x2="460" y2="7" stroke="#e2e2e2"/><path d="M230 1v12M224 7h12" stroke="#ccc" stroke-width="2"/></svg>

  <div class="step" style="left:115px;top:823px">
    <div class="step-icon"><svg width="36" height="40" viewBox="0 0 36 40"><circle cx="16" cy="14" r="12" fill="none" stroke="#1f3550" stroke-width="3"/><path d="M13 12v18l5-4 4 9 4-2-4-9h7z" fill="#1f3550"/></svg></div>
    <h3>Choose a Plan</h3>
    <p>There will be plans for all budgets<br>and styles.</p>
  </div>
  <div class="step" style="left:434px;top:823px">
    <div class="step-icon"><svg width="32" height="26" viewBox="0 0 32 26"><path d="M3 13l9 9L29 4" fill="none" stroke="#1f3550" stroke-width="6"/></svg></div>
    <h3>Choose How Often</h3>
    <p>Decide whether you would like to receive new<br>packages every 3 or 6 months.</p>
  </div>
  <div class="step" style="left:752px;top:823px">
    <div class="step-icon"><svg width="26" height="30" viewBox="0 0 26 30"><path d="M8 10V7a5 5 0 0110 0v3" fill="none" stroke="#1f3550" stroke-width="2.5"/><path d="M3 10h20l2 19H1z" fill="#1f3550"/></svg></div>
    <h3>Get your Pack</h3>
    <p>We'll send out your first pack right away and<br>then again every 3 or 6 months.</p>
  </div>
</section>

<section class="plans">
  <h2 class="section-title" style="top:36px;color:var(--white);font-weight:400;font-size:31px">Plans</h2>
  <svg class="divider" style="top:84px" viewBox="0 0 460 14"><line x1="0" y1="7" x2="205" y2="7" stroke="#f07b70"/><line x1="255" y1="7" x2="460" y2="7" stroke="#f07b70"/><path d="M230 1v12M224 7h12" stroke="#f5a097" stroke-width="2"/></svg>

  <article class="plan-card" style="left:131px">
    <h3>Comfort</h3>
    <div class="product-shot" style="left:20px;top:78px;width:160px;height:174px;background:linear-gradient(#eee,#d9d9d9)" role="img" aria-label="Model wearing white trunks"></div>
    <div class="product-shot" style="left:205px;top:76px;width:108px;height:75px;background:linear-gradient(#9a92a6,#6e6878)" role="img" aria-label="Grey boxer shorts"></div>
    <div class="product-shot" style="left:205px;top:179px;width:108px;height:75px;background:linear-gradient(#5a4b45,#2c2320)" role="img" aria-label="Dark brown briefs"></div>
    <div class="price">$30</div>
    <div class="get-it">Get It!</div>
  </article>

  <article class="plan-card" style="left:500px">
    <h3>Style</h3>
    <div class="product-shot" style="left:22px;top:78px;width:160px;height:174px;background:linear-gradient(135deg,#222 30%,#c33 55%,#2a3a9a 75%)" role="img" aria-label="Fan of coloured socks"></div>
    <div class="product-shot" style="left:207px;top:76px;width:106px;height:75px;background:linear-gradient(90deg,#222,#8a8a7a,#b5b09a)" role="img" aria-label="Striped socks"></div>
    <div class="product-shot" style="left:207px;top:179px;width:106px;height:75px;background:linear-gradient(90deg,#4a4f5a,#2e3a5a,#3a3a3a)" role="img" aria-label="Patterned dark socks"></div>
    <div class="price">$30</div>
    <div class="get-it">Get It!</div>
  </article>

  <ul class="perks">
    <li>Free Shipping</li>
    <li>Easy Return</li>
    <li>Cancel Whenever</li>
    <li>Satisfaction Guaranteed</li>
  </ul>
</section>

<section class="faq">
  <h2 class="section-title" style="top:1638px;color:var(--ink);font-weight:400">FAQ's</h2>
  <div class="section-title" style="top:1676px;font-size:20px;color:#555;font-weight:700">(Frequently Asked Question)</div>

  <div class="faq-card" style="left:131px;top:1730px"><h4>What is Brick Dune?</h4><p>Lorem ipsum dolor sit amet, consectetur<br>adipiscing elit, sed do eiusmod tempor<br>incididunt ut labore et dolor.</p></div>
  <div class="faq-card" style="left:451px;top:1730px"><h4>What is your<br>Satisfaction Guaranteed?</h4><p>Lorem ipsum dolor sit amet, consectetur<br>adipiscing elit, sed do eiusmod tempor<br>incididunt ut labore et dolor.</p></div>
  <div class="faq-card" style="left:770px;top:1730px"><h4>Shipping Policy?</h4><p>Lorem ipsum dolor sit amet, consectetur<br>adipiscing elit, sed do eiusmod tempor<br>incididunt ut labore et dolor.</p></div>
  <div class="faq-card" style="left:131px;top:1966px"><h4>What I do get with<br>my brick dune plan?</h4><p>Lorem ipsum dolor sit amet, consectetur<br>adipiscing elit, sed do eiusmod</p></div>
  <div class="faq-card" style="left:451px;top:1966px"><h4>Return Policy?</h4><p>Lorem ipsum dolor sit amet, consectetur<br>adipiscing elit, sed do eiusmod tempor<br>incididunt ut labore et dolor.</p></div>
  <div class="faq-card" style="left:770px;top:1966px"><h4>What about Sizing?</h4><p>Lorem ipsum dolor sit amet, consectetur<br>adipiscing elit, sed do eiusmod tempor<br>incididunt ut labore et dolor.</p></div>
</section>

<footer class="site-footer">
  <div class="links" style="left:132px">Shipping / Returns / Payment / Terms / Privacy</div>
  <div class="email" style="left:478px">holla@brickdune.com.au</div>
  <span class="social" style="left:741px;background:#3b5998"></span>
  <span class="social" style="left:784px;background:#2aa9e0"></span>
  <span class="social" style="left:828px;background:#34465d"></span>
  <span class="social" style="left:873px;background:#a0614a"></span>
  <span class="pay" style="left:935px;background:#5b9bd5"></span>
  <span class="pay" style="left:980px;background:#e8edf5"></span>
  <span class="pay" style="left:1029px;background:#4a6fb5"></span>
</footer>

</body>
</html>
```